Allied Health team of Physiotherapists & Occupational Therapists seek a business card design

We have our new logo, we now need our new business cards and stationary. Tidewell: Oedema & Family Clinic is seeking a generic card design to represent our whole team and individual cards for each therapist that incorporates our new logo to communicate our holistic approach that is calming, nuturing, supportive and welcoming.
Our Physiotherapists and Occupational Therapists assess, treat and provide education for people who are at risk of or who have lymphoedema. This is often as a result of treatment for cancer. We provide pre-operative and post-operative management and cancer rehabilitation in our Pilates studio. Our team also consists of Physiotherapists who have a strong interest in pelvic floor and continence management for both men and women.

Target Market(s)

Mainly women health conscious

Industry/Entity Type

Allied Health: Physiotherapy / Occupational Therapy

Contact Information for Business Card

Address: 14 Gallivant Ave Seabrook 3218 Phone: 84316570 fax: 8431 6578 Email: info@tidewellcareservices.com.au Website: tidewellcareservices.com.au Facebook address: facebook.com/TidewellOedemaAndFamilyCareClinic. Room to write appointments. Individual cards need to have name, office email and individual email and professional details

Requirements
Must have
• Logo as per uploaded documents

```html
<!DOCTYPE html>
<html lang="en">
<head>
<meta charset="utf-8">
<title>Tidewell: Oedema &amp; Family Clinic – Business Card</title>
<link rel="stylesheet" href="https://fonts.googleapis.com/css2?family=Nunito+Sans:ital,wght@0,300;0,400;0,600;1,400;1,800&display=swap">
<style>
  :root {
    --peach: #f8b180;
    --peach-text: #f5a775;
    --sage: #c3cec1;
    --card: #ffffff;
    --ink-soft: #555555;
    --box-line: #b9b9b9;
    --page: #ecebe8;
  }
  * { box-sizing: border-box; margin: 0; padding: 0; }
  html, body {
    width: 1200px; height: 1200px; overflow: hidden;
    background: var(--page);
    font-family: "Nunito Sans", sans-serif;
  }
  .card {
    position: absolute;
    left: 262px;
    width: 686px; height: 392px;
    background: var(--card);
    border-radius: 24px;
    overflow: hidden;
    box-shadow: 0 14px 30px rgba(0,0,0,0.18);
  }
  .card--front { top: 165px; }
  .card--back { top: 653px; }

  /* front */
  .front-wave { position: absolute; inset: 0; width: 100%; height: 100%; }
  .brand-name {
    position: absolute; left: 0; right: 0; top: 112px;
    text-align: center;
    font-size: 50px; font-weight: 300; letter-spacing: 1px;
    color: var(--peach-text);
  }
  .holder {
    position: absolute; left: 37px; top: 278px; color: #fff;
  }
  .holder__name { font-size: 26px; font-weight: 400; line-height: 1.1; }
  .holder__role { font-size: 15px; font-weight: 400; margin-top: 2px; }
  .holder__address { font-size: 17px; font-weight: 400; margin-top: 13px; margin-left: -2px; }
  .contact {
    position: absolute; right: 39px; top: 290px;
    text-align: right; color: #fff; font-size: 17px; line-height: 1.28;
  }

  /* back */
  .appt__title {
    position: absolute; left: 48px; top: 36px;
    font-size: 26px; font-weight: 600; color: var(--peach-text);
  }
  .book-online {
    position: absolute; left: 509px; top: 44px;
    width: 133px; height: 27px; border-radius: 6px;
    background: var(--peach); color: #fff;
    font-size: 16px; font-weight: 800; font-style: italic;
    display: flex; align-items: center; justify-content: center;
  }
  .watermark {
    position: absolute; left: 0; right: 0; top: 170px;
    text-align: center;
    font-size: 84px; font-weight: 300; color: var(--peach-text);
    opacity: 0.08;
  }
  .field {
    position: absolute; display: flex; align-items: flex-end;
    font-size: 15px; color: var(--peach-text);
  }
  .field__line {
    flex: 1; border-bottom: 1.5px dotted #777; margin: 0 6px 4px 10px; height: 1px;
  }
  .field--name { left: 47px; top: 94px; width: 595px; }
  .field--date { left: 47px; top: 142px; width: 316px; }
  .field--date .field__line { margin-right: 0; }
  .field--time { left: 365px; top: 142px; width: 252px; }
  .field--note { left: 47px; top: 234px; width: 602px; }
  .field--note .field__line { margin-left: 4px; }
  .field--extra { left: 47px; top: 285px; width: 602px; }
  .field--extra .field__line { margin: 0 0 4px 0; }
  .days {
    position: absolute; left: 47px; top: 192px;
    display: flex; font-size: 15px; color: var(--peach-text);
  }
  .day { display: flex; align-items: center; width: 92px; }
  .day:nth-child(6) { width: 75px; }
  .day:last-child { width: auto; }
  .day__box {
    width: 19px; height: 14px; border: 1.5px solid var(--box-line); margin-right: 8px;
  }
  .policy {
    position: absolute; left: 0; right: 0; top: 317px;
    text-align: center; font-size: 14.5px; font-style: italic;
    color: var(--ink-soft); line-height: 1.4;
  }
</style>
</head>
<body>

<section class="card card--front" aria-label="Business card front">
  <svg class="front-wave" viewBox="0 0 800 457" preserveAspectRatio="none" aria-hidden="true">
    <path d="M0 195 C 220 335, 420 355, 800 215 L800 230 C 430 365, 210 355, 0 222 Z" fill="var(--sage)"/>
    <path d="M0 226 C 210 357, 430 367, 800 220 L800 457 L0 457 Z" fill="#ffffff"/>
    <path d="M0 230 C 210 360, 430 370, 800 222 L800 457 L0 457 Z" fill="var(--peach)"/>
  </svg>
  <div class="brand-name">Tidewell</div>
  <div class="holder">
    <div class="holder__name">Maren Ashby</div>
    <div class="holder__role">Physiotherapist</div>
    <div class="holder__address">14 Gallivant Ave, Seabrook 3218</div>
  </div>
  <div class="contact">
    <div>(P) 8431 6570</div>
    <div>(F)8431 6578</div>
    <div>info@tidewellcareservices.com.au</div>
  </div>
</section>

<section class="card card--back" aria-label="Business card back">
  <div class="watermark">Tidewell</div>
  <h2 class="appt__title">Next Appointment</h2>
  <div class="book-online">Book Online</div>

  <div class="field field--name"><span>Name :</span><span class="field__line"></span></div>
  <div class="field field--date"><span>Date :</span><span class="field__line"></span></div>
  <div class="field field--time"><span>Time :</span><span class="field__line"></span><span>AM/PM</span></div>

  <div class="days">
    <span class="day"><span class="day__box"></span>Sun</span>
    <span class="day"><span class="day__box"></span>Mon</span>
    <span class="day"><span class="day__box"></span>Tue</span>
    <span class="day"><span class="day__box"></span>Wed</span>
    <span class="day"><span class="day__box"></span>Thu</span>
    <span class="day"><span class="day__box"></span>Fri</span>
    <span class="day"><span class="day__box"></span>Sat</span>
  </div>

  <div class="field field--note"><span>Note :</span><span class="field__line"></span></div>
  <div class="field field--extra"><span class="field__line"></span></div>

  <p class="policy">Please give me 24 hours notice if you are unable to keep your appointment or<br>a cancellation fee may be charged.</p>
</section>

</body>
</html>
```